Telvo Website - endlich neu?!
Aufgabenstellung
Es geht um die Gestaltung der Startseite auf Basis unseres verwendeten Magento-Templates.
Außerdem um die Gestaltung von Visitenkarte und Briefkopf.

```html
<!DOCTYPE html>
<html lang="de">
<head>
<meta charset="utf-8">
<title>Telvo – Geschäftsausstattung</title>
<link rel="stylesheet" href="https://fonts.googleapis.com/css2?family=Arimo:wght@400;700&display=swap">
<style>
  :root {
    --bg: #dcdcdc;
    --paper: #ffffff;
    --tone: #d0d0d0;
    --ink: #111111;
    --muted: #555555;
    --accent: #e30613;
    --line: #1a1a1a;
  }
  * { box-sizing: border-box; margin: 0; padding: 0; }
  html, body { width: 1200px; height: 1030px; overflow: hidden; }
  body {
    position: relative;
    background: var(--bg);
    font-family: "Arimo", Arial, sans-serif;
    color: var(--ink);
  }

  .brand-name {
    display: flex; align-items: center; gap: 10px;
    font-family: "Arimo", Arial, sans-serif;
    font-weight: 700; color: var(--ink);
    letter-spacing: 1px;
  }
  .brand-name .dot {
    width: 12px; height: 12px; border-radius: 50%;
    background: var(--accent); flex: none;
  }

  .logo-panel {
    position: absolute; left: 50px; top: 110px;
    width: 370px; height: 210px;
    background: var(--paper);
    border: 1.5px solid var(--line);
    border-radius: 110px 110px 110px 20px;
    display: flex; align-items: center; justify-content: center;
  }
  .logo-panel .brand-name { font-size: 64px; }
  .logo-panel .dot { width: 18px; height: 18px; }

  .card {
    position: absolute; left: 50px;
    width: 380px; height: 230px;
    background: var(--tone);
    overflow: hidden;
  }
  .card svg { position: absolute; inset: 0; }
  .card-front { top: 400px; }
  .card-front .brand-name {
    position: absolute; left: 150px; top: 80px; font-size: 54px;
  }
  .card-front .dot { width: 16px; height: 16px; }

  .card-back { top: 710px; }
  .card-back .details {
    position: absolute; right: 22px; top: 22px;
    text-align: right; font-weight: 700; color: var(--muted);
    font-size: 12.5px; line-height: 16px; letter-spacing: 0.6px;
  }
  .card-back .person {
    display: flex; align-items: center; justify-content: flex-end; gap: 8px;
    color: var(--accent); font-size: 14px; letter-spacing: 1.2px;
    margin-bottom: 20px;
  }
  .card-back .person .dot {
    width: 11px; height: 11px; border-radius: 50%; background: var(--accent);
  }
  .card-back .block { margin-bottom: 18px; }
  .card-back .label { font-weight: 400; }

  .letterhead {
    position: absolute; left: 490px; top: 40px;
    width: 680px; height: 962px;
    background: var(--tone);
    overflow: hidden;
  }
  .letterhead > svg { position: absolute; inset: 0; }
  .letterhead .brand-name {
    position: absolute; right: 40px; top: 100px; font-size: 40px;
  }
  .recipient {
    position: absolute; left: 88px; top: 210px;
    font-size: 13px; line-height: 18px;
  }
  .letter {
    position: absolute; left: 92px; top: 362px; width: 540px;
    font-size: 13px; line-height: 18px;
  }
  .letter .subject { font-weight: 700; }
  .letter p { margin-bottom: 18px; }
  .letter .salutation { margin-bottom: 18px; }
  .letter .sign { margin-top: 18px; }

  .letter-footer {
    position: absolute; left: 84px; right: 30px; top: 880px;
    display: grid; grid-template-columns: 150px 160px 140px 1fr;
    font-size: 10px; line-height: 15px; color: var(--ink);
    white-space: nowrap;
  }
  .letter-footer strong { font-weight: 700; }
  .bank { display: grid; grid-template-columns: 40px auto; align-content: start; }
  .bank .head { grid-column: 1 / 3; font-weight: 700; margin-bottom: 3px; }
  .bank .num { font-weight: 700; }
</style>
</head>
<body>

  <div class="logo-panel">
    <div class="brand-name">Telvo<span class="dot"></span></div>
  </div>

  <div class="card card-front">
    <svg width="380" height="230" viewBox="0 0 380 230" aria-hidden="true">
      <path d="M120,230 C100,120 140,20 240,14 C320,10 370,60 380,110 L380,230 Z" fill="var(--paper)"/>
      <path d="M120,230 C100,120 140,20 240,14 C320,10 370,60 380,110" fill="none" stroke="var(--line)" stroke-width="1.2"/>
    </svg>
    <div class="brand-name">Telvo<span class="dot"></span></div>
  </div>

  <div class="card card-back">
    <svg width="380" height="230" viewBox="0 0 380 230" aria-hidden="true">
      <path d="M180,0 C130,60 140,190 240,230 L380,230 L380,0 Z" fill="var(--paper)"/>
      <path d="M180,0 C130,60 140,190 240,230" fill="none" stroke="var(--line)" stroke-width="1.2"/>
    </svg>
    <div class="details">
      <div class="person"><span class="dot"></span>MIRA HELLWIG</div>
      <div class="block">Lindenhofweg 14<br>30165 Hannover</div>
      <div class="block"><span class="label">Fon</span> (0511) 27 630 418<br><span class="label">Fax</span> (0511) 27 630 419</div>
      <div>Mira@Telvo.de<br>www.Telvo.de</div>
    </div>
  </div>

  <div class="letterhead">
    <svg width="680" height="962" viewBox="0 0 680 962" aria-hidden="true">
      <path d="M0,170 C180,70 470,60 600,250 C690,380 700,700 650,962 L0,962 Z" fill="var(--paper)"/>
      <path d="M0,170 C180,70 470,60 600,250 C690,380 700,700 650,962" fill="none" stroke="var(--line)" stroke-width="1.2"/>
    </svg>
    <div class="brand-name">Telvo<span class="dot"></span></div>

    <div class="recipient">
      Herr Mustermann<br>
      Musterstraße 22<br>
      40022 Musterhausen
    </div>

    <div class="letter">
      <div class="subject">Corporate Design für Telvo</div>
      <div class="salutation">Sehr geehrte Frau Mustermann,</div>
      <p>herzlichen Dank für die Logos. Die Logik der Logos ist logisch und ich komme zu der logischen Endlogik, dass ich die Qual der Wahl habe. Der Briefbogen oder das Briefpapier oder der Kopfbogen ist ein ein- oder beidseitig vorgedruckter Formatpapierbogen für die private oder geschäftliche briefliche Korrespondenz, dem individuell ein Text und/oder Daten hinzugefügt werden müssen. Der Briefbogen dient der Arbeitsvereinfachung im Büro und der Corporate Identity des Absenders. Der Briefbogen ist ein endbeschnittenes und ausgerüstetes Rohprodukt. Briefbogen bestehen in der Regel aus besserem Schreib- oder Kopierpapier mit einem zuvor in einem beliebigen Druckverfahren aufgebrachten Briefkopf, der meist relevante Absenderangaben enthält.</p>
      <p>Das Geschäftsbriefpapier enthält typischerweise folgende Absenderangaben: den Unternehmensnamen mit Rechtsform, die Postanschrift, die Kommunikationsdaten (zum Beispiel Telefonnummer, E-Mail-Adresse und Telefax), ein Logo (falls üblich), ein reserviertes Feld für die Empfängeranschrift, eine Referenzzeile.</p>
      <p>Mit freundlichem Gruß</p>
      <div class="sign">Martina Musterfrau</div>
    </div>

    <div class="letter-footer">
      <div><strong>Telvo</strong><br>Lindenhofweg 14<br>30165 Hannover</div>
      <div>Fon (0511) 27 630 418<br>Fax (0511) 27 630 419<br><strong>Mira@Telvo.de</strong></div>
      <div class="bank">
        <span class="head">Nordwest Bank</span>
        <span>BLZ</span><span class="num">253 901 72</span>
        <span>Kto.</span><span class="num">48 211 590</span>
      </div>
      <div class="bank">
        <span class="head">Kreissparkasse Lindhorst</span>
        <span>BLZ</span><span class="num">253 901 72</span>
        <span>Kto.</span><span class="num">48 211 590</span>
      </div>
    </div>
  </div>

</body>
</html>
```